Catalogue Design Project

We need a catalog design for a new private university called Redwell Institute Bayshore (see website www.rwi-bs.org). The catalog should be about 30 pages maximum and will include items such as General Information, Academic schedule, department descriptions, program descriptions, course descriptions, school policies, student services, admissions, San diego Lifestyle, etc.
I will provide the text but I need a professional design with regard to page layouts. I have provided some examples.
Ok, i posted the catalog content, just missing course descriptions.
Target Market(s)
Young Professionals, Foreign Students
Industry/Entity Type
University
Look and feel
Each slider illustrates characteristics of the customer's brand and the style your logo design should communicate.

```html
<!DOCTYPE html>
<html lang="en">
<head>
<meta charset="utf-8">
<title>Redwell Institute Bayshore – General Information</title>
<link href="https://fonts.googleapis.com/css2?family=Arimo:wght@700&family=Carlito:wght@400;700&display=swap" rel="stylesheet">
<style>
  :root {
    --page: #ffffff;
    --ink: #1a1a1a;
    --heading: #111111;
    --navy: #1f4e8c;
    --navy-dark: #173f73;
    --rule: #6f93bf;
    --footer-ink: #8a8a8a;
  }
  * { margin: 0; padding: 0; box-sizing: border-box; }
  html, body { width: 927px; height: 1200px; overflow: hidden; background: var(--page); }
  .page { position: relative; width: 927px; height: 1200px; background: var(--page); }

  .top-rule { position: absolute; left: 0; top: 32px; width: 927px; height: 2px; background: var(--rule); }
  .hero { position: absolute; top: 34px; height: 160px; }
  .hero--campus { left: 0; width: 391px; background: linear-gradient(180deg, #3b4a2a 0%, #4f6a2c 45%, #6f9233 100%); }
  .hero--students { left: 397px; width: 232px; background: linear-gradient(180deg, #6b5a48 0%, #b58c6c 50%, #d8d2c8 100%); }
  .hero--graduate { left: 635px; width: 292px; background: linear-gradient(180deg, #9bb0c6 0%, #4a4a55 50%, #263d6e 100%); }
  .hero-rule { position: absolute; left: 0; top: 194px; width: 927px; height: 2px; background: var(--rule); }

  .section-tab { position: absolute; left: 324px; top: 194px; width: 334px; height: 38px; }
  .section-tab span {
    position: absolute; inset: 0; display: flex; align-items: center; justify-content: center;
    font-family: "Carlito", sans-serif; font-size: 26px; color: #fff; letter-spacing: 0.3px;
  }

  .heading {
    position: absolute; font-family: "Arimo", sans-serif; font-weight: 700;
    font-size: 26px; color: var(--heading); text-align: center; letter-spacing: 0.5px;
  }
  .body-text {
    position: absolute; font-family: "Carlito", sans-serif; font-size: 19px;
    line-height: 30.6px; color: var(--ink); text-align: justify;
  }
  .indent { text-indent: 60px; }

  .classroom-photo {
    position: absolute; left: 465px; top: 288px; width: 462px; height: 297px;
    background: linear-gradient(180deg, #e6e6e6 0%, #cfcfcf 45%, #3a3a3a 70%, #5a5a5a 100%);
  }

  .footer-rule { position: absolute; left: 0; top: 1160px; width: 927px; height: 2px; background: var(--rule); }
  .footer-label {
    position: absolute; right: 38px; top: 1171px; font-family: "Carlito", sans-serif;
    font-size: 13px; color: var(--footer-ink); letter-spacing: 0.4px;
  }
</style>
</head>
<body>
<div class="page">
  <div class="top-rule"></div>
  <div class="hero hero--campus" role="img" aria-label="Students relaxing on a grassy campus lawn under trees"></div>
  <div class="hero hero--students" role="img" aria-label="Group of smiling students holding books in a library"></div>
  <div class="hero hero--graduate" role="img" aria-label="Graduate in cap and gown by a canal"></div>
  <div class="hero-rule"></div>

  <div class="section-tab">
    <svg width="334" height="38" viewBox="0 0 334 38" aria-hidden="true">
      <polygon points="0,0 334,0 318,38 16,38" fill="var(--navy)"/>
    </svg>
    <span>GENERAL INFORMATION</span>
  </div>

  <h2 class="heading" style="left:56px; top:272px; width:391px;">FACILITIES</h2>
  <p class="body-text" style="left:56px; top:316px; width:391px;">Redwell Institute Bayshore is located at 418 Marlin Street, in the heart of downtown Bayshore's financial district. Our headquarters and classrooms have been completed renovated and we are proud to have one of the most professional and modern-looking campuses in Bayshore. Security is also a major part of RWIB's campus plan; security cameras monitor common areas and students must have a valid ID card to enter the facility.</p>
  <p class="body-text indent" style="left:56px; top:652px; width:391px;">In addition to providing students with free high-speed Wi-Fi, high-tech classrooms, traditional business classrooms, a computer lab and free beverages, the building currently hosts a restaurant, executives suites, and a fitness club. Minutes away from the Bayshore Trolley, Harborline bus stops and major freeways, RWIB is frequently located for all visitors and means of transportation.</p>

  <h2 class="heading" style="left:56px; top:978px; width:391px;">STAFF</h2>
  <p class="body-text" style="left:56px; top:1022px; width:391px;">Our information desk is available during normal business hours 9:00am to 10:00pm to help students with any questions that may</p>

  <div class="classroom-photo" role="img" aria-label="Empty modern classroom with rows of desks and black chairs"></div>

  <p class="body-text" style="left:477px; top:600px; width:414px;">need including but not limited to admissions and requirements, class registration, directions to and from campus, and general information about the university and faculty.</p>

  <h2 class="heading" style="left:477px; top:762px; width:414px;">LIBRARY</h2>
  <p class="body-text" style="left:477px; top:812px; width:414px;">Students at Redwell Institute Bayshore have the advantage of utilizing both the nearby downtown Bayshore Library and our online services. We currently partner with an online library that allows students to search through thousands of articles and research materials for their courses that they wouldn't otherwise have access to. Students can also purchase BSCU and HVSU library cards and be reimbursed.</p>

  <div class="footer-rule"></div>
  <div class="footer-label">3::: REDWELL INSTITUTE BAYSHORE</div>
</div>
</body>
</html>
```